Grey Fennel Medical Website to make connecting and communicating easier

To create a unique, user-friendly, professional website for patients and professionals to access education/ information, forms, appointments, contact details, and data about us, and for us to have the capacity to link to various cloud-based platforms.
To use the logo design and colour scheme we have just sourced.

WEBSITE to be eye catching, Inspiring and alluring
- efficient and logical
- professional and trustworthy appearance
- health focus "living health matters"
- user friendly
- ability to link with cloud-based software and video conferencing tools/ telehealth
- colours- black/ white teal and ?silver

PAGES:
page 1 - Our clinic and staff, services offered, contact us- address/ map / contact details- social media connections
page 2- patients and visitors - New patient forms to complete, news and patient informtion (educatinal)
page 3 - health professionals -referral forms, research and education
page 3- online appointments
page 4 - Quick links - partners, other services
page 5- privacy policy, disclaimer

HI, Could we please extend the deadline another 5 days, so sorry just struggling with my workload to be able to keep up and I am wanting to liaise more with the designer that I will choose. I am so happy with SketchHarbor and all the designers - thank you! Thank you so much!!

Target Market(s)

Patients - mostly over 60's so the website must be minimal clicks and simple to navigate
Professionals - for education and access forms

Industry/Entity Type

Health Care

Coding

Coded - Design and coding required

Number of Pages Required

5+ page

Font styles to use
Sans Serif
Script

Colors
33b8a4
86cfc6

Requirements
Must have
• WEBSITE to be eye catching, Inspiring and alluring
- efficient and logical
- user friendly

WEBSITE - professional and user friendly
- ability to link with cloud based software and videoconferencing/ telehealth
Nice to have
• clean and crisp presentation
happy for an innovative look
room to add more services and ability to link pages and resources
Should not have
• Please ensure the website is not:
clunky
difficult to navigate
common and cheap looking

```html
<!DOCTYPE html>
<html lang="en">
<head>
<meta charset="utf-8">
<title>Grey Fennel Medical</title>
<link href="https://fonts.googleapis.com/css2?family=Domine:wght@400;700&family=Poppins:wght@400;500;600&family=Rubik:wght@800&display=swap" rel="stylesheet">
<style>
:root{
  --teal:#33b5a1;
  --teal-soft:#86cfc6;
  --teal-pale:#eef6f5;
  --field:#e6f2f0;
  --ink:#1d2322;
  --ink-dark:#1d3a34;
  --muted:#6f7573;
  --white:#ffffff;
  --line:#dfe8e6;
}
*{box-sizing:border-box;margin:0;padding:0}
html,body{width:1200px;height:4231px;overflow:hidden}
body{position:relative;background:var(--white);font-family:'Poppins',sans-serif;color:var(--ink)}
.abs{position:absolute}
.serif{font-family:'Domine',serif}
.teal{color:var(--teal)}
.photo{position:absolute;border-radius:6px}

/* top bar */
.topbar{left:0;top:0;width:1200px;height:33px;background:var(--teal);z-index:2}
.topbar .dot{position:absolute;top:10px;width:13px;height:13px;border-radius:50%;border:1.5px solid var(--white)}
.topbar .info{position:absolute;top:8px;color:var(--white);font-family:'Domine',serif;font-size:13px;white-space:nowrap}
.topbar .sep{position:absolute;top:0;width:1px;height:33px;background:rgba(255,255,255,.35)}

/* nav */
.logo{left:52px;top:46px;width:150px;text-align:center;font-family:'Domine',serif;font-size:20px;line-height:26px;color:var(--ink);z-index:2}
.menu{position:absolute;left:0;top:0;z-index:2}
.menu a{position:absolute;top:66px;font-size:11.5px;color:#4a504e;text-decoration:none;white-space:nowrap}
.menu a.active{color:var(--teal)}
.menu a.active::after{content:"";position:absolute;left:8px;right:8px;top:22px;height:2px;background:var(--teal)}

.btn{position:absolute;display:flex;height:38px;border-radius:4px;overflow:hidden;font-family:'Domine',serif;font-size:13px;color:var(--white);letter-spacing:.3px;z-index:2;white-space:nowrap}
.btn .label{flex:1;background:var(--teal);display:flex;align-items:center;justify-content:center}
.btn .arrow{width:38px;background:var(--ink-dark);display:flex;align-items:center;justify-content:center}

/* hero */
.hero-panel{left:680px;top:33px;width:520px;height:640px;background:var(--teal-pale);z-index:0}
.hero-kicker{left:62px;top:264px;font-family:'Domine',serif;font-size:17px}
.hero-title{left:60px;top:298px;font-family:'Rubik',sans-serif;font-weight:800;font-size:40px;line-height:48px;letter-spacing:.3px;color:var(--ink);white-space:nowrap}
.hero-title span{color:var(--teal)}
.scroll-line{left:1172px;top:392px;width:1px;height:92px;background:var(--teal)}
.scroll-text{left:1132px;top:522px;transform:rotate(-90deg);font-size:11px;color:var(--ink);white-space:nowrap}

/* about */
.about{left:0;top:710px;width:1200px;height:467px;background:var(--teal-pale)}
.kicker{font-family:'Domine',serif;font-size:14px;color:var(--teal)}
.h2{font-family:'Domine',serif;font-size:30px;color:var(--ink);white-space:nowrap}
.lead{font-size:13px;line-height:21px;color:var(--ink)}
.lorem{font-size:11px;line-height:19.5px;color:var(--muted)}
.tile{position:absolute;background:var(--white);border-radius:6px;box-shadow:0 4px 14px rgba(0,0,0,.06);text-align:center;font-family:'Domine',serif;font-size:14px;line-height:20px}
.tile .ring{width:60px;height:60px;margin:22px auto 12px;border-radius:50%;border:2px solid var(--teal);display:flex;align-items:center;justify-content:center}
.tile .ring i{width:48px;height:48px;border-radius:50%;background:var(--teal);display:flex;align-items:center;justify-content:center}
.sidebar{left:1108px;top:818px;width:32px;height:116px;background:var(--white);border-radius:16px;box-shadow:0 3px 10px rgba(0,0,0,.07)}

/* services */
.center{left:0;width:1200px;text-align:center}
.svc{position:absolute;width:225px;height:202px;border-radius:6px;overflow:hidden}
.svc .tag{position:absolute;left:0;bottom:0;width:150px;height:32px;background:rgba(30,36,35,.78);color:var(--white);font-family:'Domine',serif;font-size:13px;padding:8px 0 0 18px;white-space:nowrap}
.svc .tag.clear{background:none;bottom:18px}

/* team */
.team-bg{left:0;top:2090px;width:375px;height:265px;background:var(--teal-pale)}
.social-sq{position:absolute;width:28px;height:28px;border:1.5px solid var(--teal);border-radius:3px}
.round{position:absolute;width:35px;height:35px;border-radius:50%;display:flex;align-items:center;justify-content:center}

/* why us */
.why{left:0;top:2434px;width:1200px;height:411px;background:linear-gradient(90deg,#31b29e,#3bbba7)}
.why-list{left:128px;top:2655px;list-style:none;color:var(--white);font-family:'Domine',serif;font-size:13px}
.why-list li{display:flex;align-items:center;height:32.5px}
.why-list svg{margin-right:18px}

/* contact */
.form-card{left:172px;top:3065px;width:788px;height:360px;border:1.5px solid var(--line);border-radius:6px;background:var(--white)}
.field{position:absolute;height:32px;border-radius:16px;background:var(--field);font-size:10px;color:#7b8381;padding:9px 0 0 16px}

/* footer */
.foot-title{font-family:'Domine',serif;font-size:16px;color:var(--ink);white-space:nowrap}
.foot-list{list-style:none;font-size:11px;line-height:21px;color:#6a706e}
.foot-list li::before{content:"";display:inline-block;width:5px;height:5px;border-radius:50%;background:var(--teal);margin:0 14px 2px 0}
.copy{left:0;top:4183px;width:1200px;height:48px;background:var(--teal);color:var(--white);font-size:11px;text-align:center;padding-top:16px}
</style>
</head>
<body>

<!-- hero backdrop -->
<div class="abs hero-panel"></div>

<!-- top bar -->
<header>
  <div class="abs topbar">
    <span class="sep" style="left:60px"></span>
    <span class="dot" style="left:69px"></span>
    <span class="dot" style="left:104px"></span>
    <span class="dot" style="left:139px"></span>
    <span class="sep" style="left:163px"></span>
    <svg class="abs" style="left:866px;top:10px" width="14" height="14" viewBox="0 0 24 24"><path d="M6.6 10.8a15 15 0 0 0 6.6 6.6l2.2-2.2c.3-.3.7-.4 1-.2 1.1.4 2.3.6 3.6.6.6 0 1 .4 1 1V20c0 .6-.4 1-1 1A17 17 0 0 1 3 4c0-.6.4-1 1-1h3.5c.6 0 1 .4 1 1 0 1.3.2 2.5.6 3.6.1.3 0 .7-.2 1z" fill="#fff"/></svg>
    <span class="info" style="left:890px">+1 555 014 2680</span>
    <span class="sep" style="left:1015px"></span>
    <svg class="abs" style="left:1030px;top:10px" width="13" height="13" viewBox="0 0 24 24"><circle cx="12" cy="7" r="5" fill="#fff"/><path d="M2 23c0-6 4.5-9 10-9s10 3 10 9z" fill="#fff"/></svg>
    <span class="info" style="left:1052px;font-size:12px">Member Login</span>
  </div>

  <div class="abs logo">Grey Fennel<br>Medical</div>
  <nav class="menu">
    <a class="active" style="left:265px">Home</a>
    <a style="left:320px">About Us</a>
    <a style="left:389px">Our Services</a>
    <a style="left:481px">New Patients</a>
    <a style="left:576px">Health Professional</a>
    <a style="left:704px">Online Appointment</a>
    <a style="left:834px">Contact Us</a>
  </nav>
</header>

<!-- hero -->
<section>
  <div class="btn" style="left:916px;top:56px;width:224px"><span class="label">REQUEST APPOINTMENT</span><span class="arrow"><svg width="12" height="12" viewBox="0 0 12 12"><path d="M3 1l5 5-5 5" stroke="#fff" stroke-width="1.6" fill="none"/></svg></span></div>
  <div class="photo" role="img" aria-label="Two nurses reviewing a chart beside a hospital bed" style="left:484px;top:136px;width:656px;height:517px;border-radius:0;background:linear-gradient(120deg,#c9dfe6 0%,#8fb6cf 40%,#e9eef2 75%,#d6dde3 100%)"></div>
  <p class="abs hero-kicker">We Take Your Health Seriously</p>
  <h1 class="abs hero-title">WE GENERALLY<br>CARE ABOUT YOUR<br><span>WELLBEING</span></h1>
  <div class="btn" style="left:61px;top:463px;width:164px;height:41px"><span class="label">CONTACT US</span><span class="arrow"><svg width="12" height="12" viewBox="0 0 12 12"><path d="M3 1l5 5-5 5" stroke="#fff" stroke-width="1.6" fill="none"/></svg></span></div>
  <span class="abs scroll-line"></span>
  <span class="abs scroll-text">Scroll Down</span>
</section>

<!-- about -->
<section>
  <div class="abs about"></div>
  <p class="abs kicker" style="left:163px;top:808px">About Us</p>
  <h2 class="abs h2" style="left:161px;top:833px">Grey Fennel Medical</h2>
  <p class="abs lead" style="left:165px;top:890px;width:340px">We offer complete healthcare to individuals with various health concerns.</p>
  <p class="abs lorem" style="left:165px;top:940px;width:355px">Lorem Ipsum has been the industry's standard dummy text ever since the 1500s, when an unknown printer took a galley of type and scrambled it to make a type specimen book. It has survived not only five centuries, but also the leap into electronic typesetting, remaining.</p>
  <div class="btn" style="left:167px;top:1054px;width:165px;height:39px"><span class="label">LEARN MORE</span><span class="arrow"><svg width="12" height="12" viewBox="0 0 12 12"><path d="M3 1l5 5-5 5" stroke="#fff" stroke-width="1.6" fill="none"/></svg></span></div>

  <div class="tile" style="left:681px;top:798px;width:136px;height:152px">
    <div class="ring"><i><svg width="24" height="24" viewBox="0 0 24 24" fill="none" stroke="#fff" stroke-width="1.6"><circle cx="10" cy="8" r="4"/><path d="M3 20c0-4 3-6 7-6s7 2 7 6z"/><path d="M19 6v6M16 9h6"/></svg></i></div>
    New<br>Patients
  </div>
  <div class="photo" role="img" aria-label="Clinician examining a patient's skin" style="left:833px;top:784px;width:137px;height:134px;background:linear-gradient(135deg,#e9d8cc,#b99584 60%,#7d6c66)"></div>
  <div class="photo" role="img" aria-label="Smiling family sitting together" style="left:681px;top:965px;width:136px;height:157px;background:linear-gradient(135deg,#c8bcb1,#8d6e5f 55%,#d8d2cc)"></div>
  <div class="tile" style="left:833px;top:954px;width:137px;height:153px">
    <div class="ring"><i><svg width="22" height="22" viewBox="0 0 24 24" fill="none" stroke="#fff" stroke-width="1.6"><rect x="3" y="5" width="18" height="16" rx="2"/><path d="M3 10h18M8 3v4M16 3v4M7 14h2M11 14h2M15 14h2M7 17h2M11 17h2"/></svg></i></div>
    Online<br>Appointment
  </div>

  <div class="abs sidebar">
    <svg class="abs" style="left:9px;top:16px" width="14" height="14" viewBox="0 0 24 24"><path d="M6.6 10.8a15 15 0 0 0 6.6 6.6l2.2-2.2c.3-.3.7-.4 1-.2 1.1.4 2.3.6 3.6.6.6 0 1 .4 1 1V20c0 .6-.4 1-1 1A17 17 0 0 1 3 4c0-.6.4-1 1-1h3.5c.6 0 1 .4 1 1 0 1.3.2 2.5.6 3.6.1.3 0 .7-.2 1z" fill="#33b5a1"/></svg>
    <svg class="abs" style="left:9px;top:50px" width="14" height="14" viewBox="0 0 24 24" fill="none" stroke="#9aa3a1" stroke-width="2"><path d="M12 22s7-7 7-12a7 7 0 0 0-14 0c0 5 7 12 7 12z"/><circle cx="12" cy="10" r="2.5"/></svg>
    <svg class="abs" style="left:9px;top:84px" width="14" height="14" viewBox="0 0 24 24" fill="none" stroke="#9aa3a1" stroke-width="2"><circle cx="12" cy="12" r="9"/><path d="M12 7v5l3 2"/></svg>
  </div>
</section>

<!-- services -->
<section>
  <h2 class="abs h2 center" style="top:1246px">Our Services</h2>
  <p class="abs center lorem" style="top:1292px"><span style="display:inline-block;width:360px;font-size:12px;line-height:20px">We offer complete healthcare to individuals with various health concerns.</span></p>

  <div class="svc" role="img" aria-label="General practice consultation" style="left:121px;top:1364px;background:linear-gradient(135deg,#5cc7b6,#33b5a1)"><span class="tag clear">General Practice</span></div>
  <div class="svc" role="img" aria-label="Medical staff in protective suits" style="left:366px;top:1364px;background:linear-gradient(135deg,#2d4f73,#8aa6bf 55%,#3b5674)"><span class="tag">Covid-19 Service</span></div>
  <div class="svc" role="img" aria-label="Pharmacists at a medicine shelf" style="left:610px;top:1364px;background:linear-gradient(135deg,#c9d4d6,#eef1f1 50%,#9fb0b3)"><span class="tag">Pharmacy</span></div>
  <div class="svc" role="img" aria-label="Dentist treating a young patient" style="left:853px;top:1364px;background:linear-gradient(135deg,#b1c4cc,#e6d7cf 55%,#7c8d96)"><span class="tag">Dentist</span></div>
  <div class="svc" role="img" aria-label="Physiotherapist treating a knee" style="left:121px;top:1586px;background:linear-gradient(135deg,#7c93ab,#e7e2de 55%,#9aa4ae)"><span class="tag">Phsiotherapy</span></div>
  <div class="svc" role="img" aria-label="Gloved hand examining skin on a back" style="left:366px;top:1586px;background:linear-gradient(135deg,#e1c9b7,#bda395 55%,#8f9aa1)"><span class="tag">Dermatology</span></div>
  <div class="svc" role="img" aria-label="Foot examination" style="left:610px;top:1586px;background:linear-gradient(135deg,#6b6f75,#c7a997 50%,#414651)"><span class="tag">Podiatry</span></div>
  <div class="svc" role="img" aria-label="Chiropractor consulting a patient" style="left:853px;top:1586px;background:linear-gradient(135deg,#cfd4d6,#9da9b0 50%,#e7e7e5)"><span class="tag">Chrioproactic</span></div>
</section>

<!-- team -->
<section>
  <p class="abs kicker center" style="top:1880px;font-size:13px">Meet Our Team</p>
  <h2 class="abs h2 center" style="top:1902px">Our Expert Staff</h2>
  <div class="abs team-bg"></div>
  <div class="photo" role="img" aria-label="Portrait of a smiling doctor in a white coat" style="left:232px;top:1978px;width:262px;height:271px;background:linear-gradient(160deg,#dfe9ec,#b8cbd2 55%,#f2f4f5)"></div>
  <p class="abs serif" style="left:610px;top:2008px;font-size:16px">Membr Name</p>
  <p class="abs" style="left:612px;top:2034px;font-size:11px;color:var(--muted)">Phsiotherapist</p>
  <p class="abs lorem" style="left:611px;top:2070px;width:345px">Lorem Ipsum has been the industry's standard dummy text ever since the 1500s, when an unknown printer took a galley of type and scrambled it to make a type specimen book. It has survived not only .</p>
  <span class="social-sq" style="left:612px;top:2176px"></span>
  <span class="social-sq" style="left:649px;top:2176px"></span>
  <span class="social-sq" style="left:685px;top:2176px"></span>
  <span class="round" style="left:1088px;top:2067px;border:1.5px solid #b9c2c0"><svg width="10" height="10" viewBox="0 0 10 10"><path d="M3 1l4 4-4 4" stroke="#555" stroke-width="1.3" fill="none"/></svg></span>
  <span class="round" style="left:1088px;top:2111px;border:1.5px solid #333"><svg width="10" height="10" viewBox="0 0 10 10"><path d="M7 1L3 5l4 4" stroke="#333" stroke-width="1.3" fill="none"/></svg></span>
</section>

<!-- why us -->
<section>
  <div class="abs why"></div>
  <div class="abs" role="img" aria-label="Patients on a video consultation with a doctor on screen" style="left:590px;top:2450px;width:610px;height:395px;background:linear-gradient(120deg,rgba(59,187,167,0) 0%,#8fb9b4 25%,#cfdad9 55%,#5d7a8c 80%,#3bbba7 100%)"></div>
  <p class="abs serif" style="left:126px;top:2504px;font-size:13px;color:var(--white)">Why Us ?</p>
  <h2 class="abs serif" style="left:124px;top:2526px;font-size:31px;font-weight:400;color:var(--white);white-space:nowrap">Education/Information</h2>
  <p class="abs" style="left:127px;top:2576px;width:380px;font-size:11px;line-height:21px;color:var(--white)">Lorem Ipsum has been the industry's standard dummy text ever since the 1500s, when an unknown printer took a galley of type and scrambled it to make a type specimen book.</p>
  <ul class="abs why-list">
    <li><svg width="16" height="16" viewBox="0 0 16 16"><circle cx="8" cy="8" r="7" fill="none" stroke="#fff" stroke-width="1.4"/><path d="M4.8 8.2l2.2 2.2 4.2-4.4" fill="none" stroke="#fff" stroke-width="1.5"/></svg>Medical Prescription</li>
    <li><svg width="16" height="16" viewBox="0 0 16 16"><circle cx="8" cy="8" r="7" fill="none" stroke="#fff" stroke-width="1.4"/><path d="M4.8 8.2l2.2 2.2 4.2-4.4" fill="none" stroke="#fff" stroke-width="1.5"/></svg>Modern Technology</li>
    <li><svg width="16" height="16" viewBox="0 0 16 16"><circle cx="8" cy="8" r="7" fill="none" stroke="#fff" stroke-width="1.4"/><path d="M4.8 8.2l2.2 2.2 4.2-4.4" fill="none" stroke="#fff" stroke-width="1.5"/></svg>Online Education</li>
    <li><svg width="16" height="16" viewBox="0 0 16 16"><circle cx="8" cy="8" r="7" fill="none" stroke="#fff" stroke-width="1.4"/><path d="M4.8 8.2l2.2 2.2 4.2-4.4" fill="none" stroke="#fff" stroke-width="1.5"/></svg>Webinars</li>
  </ul>
</section>

<!-- contact -->
<section>
  <p class="abs kicker" style="left:522px;top:2920px">Contact Us</p>
  <h2 class="abs h2" style="left:353px;top:2944px">Request Online Consultation</h2>
  <div class="abs form-card"></div>
  <div class="photo" role="img" aria-label="Smiling doctor with stethoscope, arms crossed" style="left:200px;top:3013px;width:250px;height:487px;border-radius:0;background:linear-gradient(180deg,rgba(255,255,255,0) 0%,#e9eef2 20%,#d2dbe3 60%,#b9a98f 100%)"></div>
  <div class="field" style="left:513px;top:3122px;width:194px">First Name *</div>
  <div class="field" style="left:719px;top:3122px;width:194px">Last Name *</div>
  <div class="field" style="left:513px;top:3166px;width:194px">Enter Email*</div>
  <div class="field" style="left:719px;top:3166px;width:194px">Phone Number *</div>
  <div class="field" style="left:513px;top:3209px;width:194px">Choose Doctor *</div>
  <div class="field" style="left:719px;top:3209px;width:194px">Choose Department *</div>
  <div class="field" style="left:513px;top:3250px;width:400px;height:65px;border-radius:16px">Message</div>
  <div class="btn" style="left:513px;top:3328px;width:133px;height:37px"><span class="label">SUBMIT</span><span class="arrow"><svg width="12" height="12" viewBox="0 0 12 12"><path d="M3 1l5 5-5 5" stroke="#fff" stroke-width="1.6" fill="none"/></svg></span></div>
</section>

<!-- map -->
<div class="abs" role="img" aria-label="Street map showing the clinic location" style="left:0;top:3502px;width:1200px;height:375px;background:linear-gradient(135deg,#e4e6e7,#d9dcdd 50%,#e6e8e9)"></div>

<!-- footer -->
<footer>
  <p class="abs serif" style="left:62px;top:3920px;font-size:18px;white-space:nowrap">Grey Fennel <span class="teal">Medical</span></p>
  <svg class="abs" style="left:61px;top:3970px" width="15" height="17" viewBox="0 0 24 24" fill="none" stroke="#33b5a1" stroke-width="2"><path d="M12 22s7-7 7-12a7 7 0 0 0-14 0c0 5 7 12 7 12z"/><circle cx="12" cy="10" r="2.5"/></svg>
  <p class="abs teal" style="left:98px;top:3966px;font-size:11px">Grey Fennel Medical</p>
  <p class="abs" style="left:98px;top:3987px;font-size:11px;color:#6a706e">100 - Lorem ipsum text print</p>
  <svg class="abs" style="left:61px;top:4022px" width="15" height="15" viewBox="0 0 24 24"><path d="M6.6 10.8a15 15 0 0 0 6.6 6.6l2.2-2.2c.3-.3.7-.4 1-.2 1.1.4 2.3.6 3.6.6.6 0 1 .4 1 1V20c0 .6-.4 1-1 1A17 17 0 0 1 3 4c0-.6.4-1 1-1h3.5c.6 0 1 .4 1 1 0 1.3.2 2.5.6 3.6.1.3 0 .7-.2 1z" fill="#33b5a1"/></svg>
  <p class="abs" style="left:98px;top:4021px;font-size:11px">555 014 2680</p>
  <svg class="abs" style="left:61px;top:4052px" width="16" height="12" viewBox="0 0 16 12"><rect width="16" height="12" rx="1.5" fill="#33b5a1"/><path d="M1 1l7 5 7-5" stroke="#fff" stroke-width="1.3" fill="none"/></svg>
  <p class="abs" style="left:98px;top:4050px;font-size:11px;color:#6a706e">info@greyfennel.com</p>
  <span class="abs" style="left:61px;top:4090px;width:28px;height:28px;background:var(--teal);border-radius:3px"></span>
  <span class="abs" style="left:97px;top:4090px;width:28px;height:28px;background:var(--teal);border-radius:3px"></span>
  <span class="abs" style="left:133px;top:4090px;width:28px;height:28px;background:var(--teal);border-radius:3px"></span>

  <p class="abs foot-title" style="left:336px;top:3922px">Sitemap</p>
  <ul class="abs foot-list" style="left:336px;top:3957px">
    <li>Home</li><li>About Us</li><li>Our Services</li><li>New Patients</li><li>Health Professional</li><li>Online Appointment</li><li>Contact</li>
  </ul>

  <p class="abs foot-title" style="left:612px;top:3922px">Our Services</p>
  <ul class="abs foot-list" style="left:612px;top:3957px">
    <li>General Practice</li><li>Covid-19 Service</li><li>Pharmacy</li><li>Dentists</li><li>Phsiotherapy</li><li>Dermatology</li><li>Podiatry</li><li>Chiropractic</li>
  </ul>

  <p class="abs foot-title" style="left:886px;top:3922px">Newsletter Signup !</p>
  <p class="abs" style="left:886px;top:3960px;width:260px;font-size:10.5px;line-height:21px;color:#6a706e">Would you like to receive update for signup our newsletter !</p>
  <div class="abs" style="left:886px;top:4018px;width:253px;height:38px;border:1.5px solid var(--line);border-radius:4px;font-size:10px;color:#7b8381;padding:12px 0 0 14px">Enter Email *</div>
  <div class="btn" style="left:886px;top:4068px;width:150px;height:38px"><span class="label">SUBSCRIBE</span><span class="arrow"><svg width="12" height="12" viewBox="0 0 12 12"><path d="M3 1l5 5-5 5" stroke="#fff" stroke-width="1.6" fill="none"/></svg></span></div>

  <div class="abs copy">©Grey Fennel Medical - 2020 All rights reserved.</div>
</footer>

</body>
</html>
```